The Q Collective Business Cards

We need a sleek looking business card for our real estate company. Looking for a clean, modern, eye catching design on a standard size business card.
Updates

No more submissions please! Thank you!

Target Market(s)

General Public/Real Estate Clients

Industry/Entity Type

Real Estate

Contact Information for Business Card

Cards will be customized for each agent.

Colors

Designer to choose only greyscale colors for use in the design.

Requirements
Must have
• Black, white, gray color pallet, Photo area for headshot on the front of the card

```html
<!DOCTYPE html>
<html lang="en">
<head>
<meta charset="utf-8">
<title>The Q Collective – Business Cards</title>
<link href="https://fonts.googleapis.com/css2?family=Montserrat:wght@500;600&family=Roboto:wght@400&display=swap" rel="stylesheet">
<style>
  :root {
    --page: #2a2a2a;
    --card: #222222;
    --card-back: #1d1d1d;
    --white: #ffffff;
    --light: #e6e6e6;
    --strip: #8a8a8a;
  }
  * { margin: 0; padding: 0; box-sizing: border-box; }
  html, body { width: 1200px; height: 1138px; overflow: hidden; }
  body {
    background: var(--page);
    position: relative;
    font-family: "Roboto", Arial, sans-serif;
    color: var(--light);
  }
  .card {
    position: absolute;
    left: 289px;
    width: 622px;
    height: 376px;
    border-radius: 14px;
    overflow: hidden;
  }
  .card--front { top: 186px; background: var(--card); }
  .card--back { top: 608px; background: var(--card-back); }

  /* Front */
  .front-name {
    position: absolute;
    left: 0; right: 0; top: 170px;
    text-align: center;
    font-family: "Montserrat", Arial, sans-serif;
    font-weight: 500;
    font-size: 26px;
    letter-spacing: 5px;
    color: var(--white);
  }
  .brokerage {
    position: absolute;
    left: 28px; top: 334px;
    font-family: "Roboto", Arial, sans-serif;
    font-weight: 400;
    font-size: 10.5px;
    letter-spacing: 0.3px;
    color: var(--light);
  }

  /* Back */
  .headshot {
    position: absolute;
    left: 0; top: 0;
    width: 300px; height: 376px;
    background: linear-gradient(160deg, #1d1d1d 0%, #3b2e26 45%, #8a7466 75%, #d9d6d2 100%);
  }
  .back-strip {
    position: absolute;
    left: 300px; right: 0; bottom: 0;
    height: 10px;
    background: var(--strip);
  }
  .back-name {
    position: absolute;
    left: 326px; top: 64px;
    font-family: "Montserrat", Arial, sans-serif;
    font-weight: 500;
    font-size: 22px;
    letter-spacing: 3px;
    color: var(--white);
  }
  .agent {
    position: absolute;
    left: 326px; top: 158px;
  }
  .agent__name {
    font-family: "Montserrat", Arial, sans-serif;
    font-weight: 600;
    font-size: 23px;
    color: var(--white);
  }
  .agent__title { font-size: 15px; margin-top: 3px; color: var(--light); }
  .agent__address { font-size: 15px; line-height: 23px; margin-top: 22px; color: var(--light); }
  .contact { list-style: none; margin-top: 8px; }
  .contact li {
    display: flex; align-items: center;
    font-size: 15.5px; line-height: 24px; color: var(--light);
  }
  .contact svg { width: 14px; height: 14px; margin-right: 18px; fill: none; stroke: var(--light); stroke-width: 1.4; }
</style>
</head>
<body>

<section class="card card--front" aria-label="Card front">
  <div class="front-name">THE Q COLLECTIVE</div>
  <div class="brokerage">GREATER RIDGEPORT REALTY</div>
</section>

<section class="card card--back" aria-label="Card back">
  <div class="headshot" role="img" aria-label="Agent headshot photo area"></div>
  <div class="back-strip"></div>

  <div class="back-name">THE Q COLLECTIVE</div>

  <div class="agent">
    <div class="agent__name">Maya Delgado Hart</div>
    <div class="agent__title">Real Estate Broker</div>
    <div class="agent__address">4120 Lindell Parkway<br>Ridgeport, LA, US 70899</div>
    <ul class="contact">
      <li>
        <svg viewBox="0 0 16 16" aria-hidden="true"><path d="M2 6c0-2 2-3 6-3s6 1 6 3v1h-3V5.5H5V7H2z"/><rect x="3.5" y="8" width="9" height="5.5" rx="1"/></svg>
        +1 225-555-0148
      </li>
      <li>
        <svg viewBox="0 0 16 16" aria-hidden="true"><rect x="1.5" y="3.5" width="13" height="9"/><path d="M1.5 3.5l6.5 5 6.5-5"/></svg>
        maya@ridgeporthomes.com
      </li>
      <li>
        <svg viewBox="0 0 16 16" aria-hidden="true"><circle cx="8" cy="8" r="6.3"/><ellipse cx="8" cy="8" rx="2.7" ry="6.3"/><path d="M1.7 8h12.6"/></svg>
        www.ridgeporthomes.com
      </li>
    </ul>
  </div>
</section>

</body>
</html>
```